BildeVOLD buisnesscard

Hey :) I need a modern buisnesscard for my company BildeVOLD
It most have:
Dagligleder og Fotograf: Henrik Audun Strandvik

Mob: +4791264085
Epost: post@bildevold.example
Adresse: Kvernbakken9, 6040 Strandli

Facbook and instagram logo with text BildeVOLD

BildeVOLD logo

It Company

```html
<!DOCTYPE html>
<html lang="no">
<head>
<meta charset="utf-8">
<title>BildeVOLD – visittkort</title>
<link rel="stylesheet" href="https://fonts.googleapis.com/css2?family=Montserrat:wght@400;600;700;800&display=swap">
<style>
  :root {
    --bg: #dcdcdc;
    --paper: #f1f1f1;
    --blue: #2f86c0;
    --blue-deep: #2a78b0;
    --pink: #c9397c;
    --dark: #2b2b2b;
    --dark-line: #8a8a8a;
    --white: #ffffff;
  }
  * { margin: 0; padding: 0; box-sizing: border-box; }
  html, body { width: 1200px; height: 799px; overflow: hidden; }
  body {
    background: var(--bg);
    font-family: "Montserrat", Arial, sans-serif;
    position: relative;
  }
  .card {
    position: absolute;
    top: 110px;
    width: 330px;
    height: 580px;
    overflow: hidden;
    box-shadow: 0 8px 24px rgba(0,0,0,.25);
  }
  /* front */
  .card--front { left: 210px; background: var(--paper); }
  .front__banner {
    position: absolute;
    left: 40px; top: 0;
    width: 290px; height: 330px;
    background: linear-gradient(180deg, var(--blue), var(--blue-deep));
    clip-path: polygon(0 0, 100% 0, 100% 60%, 75% 100%, 0 100%);
  }
  .front__details {
    position: absolute;
    left: 66px; top: 38px;
    width: 250px;
    color: var(--white);
  }
  .front__name { font-size: 18px; font-weight: 700; letter-spacing: .2px; white-space: nowrap; }
  .front__role { font-size: 13px; font-weight: 400; margin-top: 4px; }
  .front__address { font-size: 13px; margin-top: 22px; line-height: 1.4; }
  .front__contacts { list-style: none; margin-top: 14px; font-size: 13px; line-height: 1.6; }
  .front__contacts li { display: flex; align-items: center; gap: 7px; }
  .front__contacts svg { width: 13px; height: 13px; flex: none; }
  .front__wordmark {
    position: absolute;
    left: 0; right: 0; top: 400px;
    text-align: center;
    font-size: 38px; font-weight: 800;
    color: var(--blue);
    letter-spacing: .5px;
  }
  .front__bar {
    position: absolute;
    right: 0; bottom: 0;
    width: 230px; height: 34px;
    background: var(--pink);
  }
  /* back */
  .card--back { left: 660px; background: var(--dark); }
  .back__wordmark {
    position: absolute;
    left: 0; right: 0; top: 230px;
    text-align: center;
    font-size: 38px; font-weight: 800;
    color: var(--blue);
    letter-spacing: .5px;
  }
  .back__social {
    position: absolute;
    left: 40px; right: 40px; top: 310px;
    display: flex; align-items: center; gap: 8px;
  }
  .back__rule { flex: 1; height: 1px; background: var(--dark-line); }
  .back__dot { width: 22px; height: 22px; border-radius: 50%; }
  .back__dot--blue { background: #3b5fa8; }
  .back__dot--pink { background: var(--pink); }
</style>
</head>
<body>

<section class="card card--front" aria-label="Visittkort forside">
  <div class="front__banner"></div>
  <div class="front__details">
    <h1 class="front__name">Henrik Audun Strandvik</h1>
    <p class="front__role">Dagligleder og Fotograf</p>
    <p class="front__address">Kvernbakken9<br>6040 Strandli</p>
    <ul class="front__contacts">
      <li>
        <svg viewBox="0 0 12 12" aria-hidden="true"><rect x="3" y="0.5" width="6" height="11" rx="1" fill="none" stroke="#fff" stroke-width="1.2"/><circle cx="6" cy="9.6" r=".7" fill="#fff"/></svg>
        +4791264085
      </li>
      <li>
        <svg viewBox="0 0 12 12" aria-hidden="true"><rect x="0.5" y="2.5" width="11" height="7" fill="#fff"/><path d="M0.5 2.5 6 7 11.5 2.5" fill="none" stroke="#2f86c0" stroke-width="1"/></svg>
        post@bildevold.example
      </li>
      <li>
        <svg viewBox="0 0 12 12" aria-hidden="true"><circle cx="6" cy="6" r="5.5" fill="#fff"/><path d="M0.5 6h11M6 .5c-2.5 3-2.5 8 0 11M6 .5c2.5 3 2.5 8 0 11" fill="none" stroke="#2f86c0" stroke-width=".8"/></svg>
        www.bildevold.example
      </li>
    </ul>
  </div>
  <div class="front__wordmark">BildeVOLD</div>
  <div class="front__bar"></div>
</section>

<section class="card card--back" aria-label="Visittkort bakside">
  <div class="back__wordmark">BildeVOLD</div>
  <div class="back__social">
    <span class="back__rule"></span>
    <span class="back__dot back__dot--blue"></span>
    <span class="back__dot back__dot--pink"></span>
    <span class="back__rule"></span>
  </div>
</section>

</body>
</html>
```